Budget Brand Responsive Website

Flat vector style website needed for value based IT support company. looking for clean, illustration intensive based design. Current test site can be found at www.bright-mend.co.uk and holding page it www.brightmend.co.uk this will show text and services, please feel free to use placeholder text if you think we need alternative text in places. Emphasis should be on low cost support and services listed on the site, would be nice to see costs in bold images. important colors are the blue, orange and white, see holding page and attached image of an advert

It Company

```html
<!DOCTYPE html>
<html lang="en">
<head>
<meta charset="utf-8">
<title>Bright Mend – IT Support</title>
<link href="https://fonts.googleapis.com/css2?family=Open+Sans:wght@400;600;700&display=swap" rel="stylesheet">
<style>
:root{
  --blue:#2f5f9f;
  --blue-dark:#2c5591;
  --orange:#e8772e;
  --white:#ffffff;
  --text:#555b63;
  --muted:#8a9099;
  --line:#e3e6ea;
  --grey-bg:#eef0f3;
  --tech-bg:#e4ebf2;
}
*{box-sizing:border-box;margin:0;padding:0}
html,body{width:1200px;height:2556px;overflow:hidden}
body{font-family:"Open Sans",Arial,sans-serif;color:var(--text);background:var(--white);position:relative}
.site-header{position:absolute;top:0;left:0;width:1200px;height:88px;display:flex;align-items:center;justify-content:space-between;padding:0 40px;background:var(--white)}
.brand{font-weight:400;font-size:28px;color:var(--blue)}
.main-nav{display:flex;gap:14px}
.main-nav a{font-size:15px;font-weight:600;color:var(--blue);text-decoration:none;padding:10px 18px;border:2px solid transparent}
.main-nav a.active{border-color:var(--orange);color:var(--orange)}
.hero{position:absolute;top:88px;left:0;width:1200px;height:672px;background:linear-gradient(120deg,#dfe6ee 0%,#aebdcc 45%,#6f8095 100%)}
.hero-title{position:absolute;left:848px;top:390px;color:var(--white);font-size:46px;line-height:56px;font-weight:400;letter-spacing:1px}
.slider-arrow{position:absolute;top:304px;width:44px;height:44px;border-radius:50%;background:var(--orange);display:flex;align-items:center;justify-content:center}
.slider-arrow.prev{left:-10px}
.slider-arrow.next{right:-10px}
.dots{position:absolute;left:0;width:100%;display:flex;justify-content:center;gap:10px}
.dots span{width:12px;height:12px;border-radius:50%;background:rgba(255,255,255,.8)}
.dots span.on{background:transparent;border:2px solid var(--white)}
.section-title{position:absolute;left:0;width:1200px;text-align:center;font-size:26px;font-weight:400;color:var(--blue)}
.title-rule{position:absolute;left:570px;width:60px;height:2px;background:var(--orange)}
.services{position:absolute;top:880px;left:56px;width:1088px;display:flex}
.service{flex:1;text-align:center;padding:0 26px;border-right:1px solid var(--line)}
.service:last-child{border-right:none}
.service h3{font-size:17px;font-weight:600;color:var(--orange);margin:14px 0 16px}
.service p{font-size:14px;line-height:24px;color:var(--muted)}
.services-dots{top:1160px}
.services-dots span{background:#d4d8de}
.services-dots span.on{border-color:var(--orange);background:transparent}
.pricing-band{position:absolute;top:1224px;left:0;width:1200px;height:556px;background:var(--grey-bg)}
.price-cards{position:absolute;top:1368px;left:104px;width:992px;display:flex;gap:16px}
.price-card{flex:1;background:var(--white);height:356px;display:flex;flex-direction:column;align-items:center}
.price-card h3{width:100%;background:var(--orange);color:var(--white);text-align:center;font-size:15px;font-weight:700;padding:14px 0}
.price-card h4{font-size:14px;font-weight:700;color:#3a3f45;text-align:center;padding:18px 20px 12px;line-height:22px;height:82px;display:flex;align-items:center}
.price-card ul{list-style:none;width:100%;padding:0 22px}
.price-card li{font-size:13px;padding:11px 0 11px 14px;border-top:1px solid var(--line);position:relative}
.price-card li::before{content:"";position:absolute;left:0;top:18px;width:5px;height:5px;border-radius:50%;background:var(--orange)}
.btn-outline{display:inline-block;margin-top:auto;margin-bottom:22px;font-size:13px;font-weight:700;color:var(--orange);border:2px solid var(--orange);padding:8px 22px;letter-spacing:1px}
.tech{position:absolute;top:1780px;left:0;width:1200px;height:360px;background:var(--tech-bg)}
.tech-photo{position:absolute;right:0;top:0;width:560px;height:360px;background:linear-gradient(90deg,var(--tech-bg) 0%,#c9d4de 40%,#b4c1cd 100%)}
.tech h2{position:absolute;left:132px;top:60px;font-size:26px;font-weight:400;color:var(--blue)}
.tech p{position:absolute;left:132px;top:112px;width:400px;font-size:14px;line-height:24px;color:var(--text)}
.tech .btn-light{position:absolute;left:132px;top:246px;font-size:13px;font-weight:600;color:var(--muted);border:2px solid #c5ccd4;padding:8px 20px;letter-spacing:1px;background:var(--white)}
.site-footer{position:absolute;top:2140px;left:0;width:1200px;height:416px;background:var(--blue-dark);color:var(--white)}
.footer-col{position:absolute;top:28px}
.footer-col h5{font-size:14px;font-weight:700;letter-spacing:1px;margin-bottom:18px}
.form-field{width:250px;height:36px;background:rgba(255,255,255,.12);border:1px solid rgba(255,255,255,.35);margin-bottom:12px;font-size:13px;padding:8px 12px;color:rgba(255,255,255,.75)}
.form-field.tall{height:84px}
.btn-submit{width:250px;height:44px;background:var(--orange);display:flex;align-items:center;justify-content:center;gap:10px;font-weight:700;font-size:15px;letter-spacing:1px}
.contact-item{display:flex;gap:10px;margin-bottom:20px;font-size:13px;line-height:20px}
.contact-item .bullet{width:7px;height:7px;background:var(--white);border-radius:50%;margin-top:7px;flex:none}
.footer-menu{list-style:none;font-size:13px;line-height:24px}
.social{display:flex;gap:10px}
.social span{width:28px;height:28px;background:rgba(255,255,255,.2)}
.copyright{position:absolute;left:40px;bottom:20px;font-size:12px;color:rgba(255,255,255,.8)}
</style>
</head>
<body>

<header class="site-header">
  <div class="brand">Bright Mend</div>
  <nav class="main-nav">
    <a class="active" href="#">HOME</a>
    <a href="#">SUPPORT</a>
    <a href="#">SERVICES</a>
    <a href="#">ABOUT</a>
    <a href="#">CONTACT</a>
  </nav>
</header>

<section class="hero">
  <div role="img" aria-label="Photo of a team of business people working at laptops in a bright office" style="position:absolute;inset:0"></div>
  <h1 class="hero-title">TRUSTED<br>TECHNOLOGY<br>PARTNERS</h1>
  <span class="slider-arrow prev"><svg width="14" height="14" viewBox="0 0 14 14"><path d="M9 2 4 7l5 5" stroke="#fff" stroke-width="2.5" fill="none"/></svg></span>
  <span class="slider-arrow next"><svg width="14" height="14" viewBox="0 0 14 14"><path d="M5 2l5 5-5 5" stroke="#fff" stroke-width="2.5" fill="none"/></svg></span>
  <div class="dots" style="top:626px"><span></span><span></span><span class="on"></span><span></span><span></span></div>
</section>

<h2 class="section-title" style="top:812px">Our Services</h2>
<span class="title-rule" style="top:858px"></span>

<div class="services">
  <div class="service">
    <svg width="34" height="34" viewBox="0 0 34 34"><path d="M6 20v-4a11 11 0 0 1 22 0v4" stroke="#e8772e" stroke-width="3" fill="none"/><rect x="3" y="18" width="7" height="11" rx="2" fill="#e8772e"/><rect x="24" y="18" width="7" height="11" rx="2" fill="#e8772e"/></svg>
    <h3>SUPPORT</h3>
    <p>Unlimited Remote Support Monitoring, backing &amp; more All from £8.50 a month.</p>
  </div>
  <div class="service">
    <svg width="34" height="34" viewBox="0 0 34 34"><rect x="12" y="3" width="10" height="18" rx="5" fill="#e8772e"/><path d="M8 16a9 9 0 0 0 18 0M17 25v6M12 31h10" stroke="#e8772e" stroke-width="2.5" fill="none"/></svg>
    <h3>VOICE</h3>
    <p>Our Cloud Phone System gives you a feature rich business telephone system over the internet.</p>
  </div>
  <div class="service">
    <svg width="34" height="34" viewBox="0 0 34 34"><circle cx="17" cy="17" r="13" stroke="#e8772e" stroke-width="2.5" fill="none"/><ellipse cx="17" cy="17" rx="6" ry="13" stroke="#e8772e" stroke-width="2" fill="none"/><path d="M4 17h26" stroke="#e8772e" stroke-width="2"/></svg>
    <h3>INTERNET</h3>
    <p>The options for all businesses to have access to faster, more reliable connectivity is huge.</p>
  </div>
  <div class="service">
    <svg width="38" height="34" viewBox="0 0 38 34"><path d="M10 28a7 7 0 0 1-1-14 10 10 0 0 1 19-2 8 8 0 0 1 1 16z" fill="#e8772e"/></svg>
    <h3>HOSTED SERVICES</h3>
    <p>Moving your office to our hosted services could not be easier, our team are on hand.</p>
  </div>
</div>
<div class="dots services-dots"><span></span><span></span><span class="on"></span><span></span></div>

<section class="pricing-band"></section>
<h2 class="section-title" style="top:1272px">Our Pricing</h2>
<span class="title-rule" style="top:1318px"></span>

<div class="price-cards">
  <div class="price-card">
    <h3>SUPPORT</h3>
    <h4>Unlimited Monthly Remote Support</h4>
    <ul><li>Workstations £8.50</li><li>Router 4G £50.00</li><li>Servers £45.00</li></ul>
    <span class="btn-outline">READ MORE</span>
  </div>
  <div class="price-card">
    <h3>VOICE</h3>
    <h4>Lower Rates And Call Charges</h4>
    <ul><li>PBX from £65.00</li><li>Line rental from £17.00</li><li>Phones numbers from £5.00</li></ul>
    <span class="btn-outline">READ MORE</span>
  </div>
  <div class="price-card">
    <h3>HOSTING</h3>
    <h4>Flexible And Secure</h4>
    <ul><li>Email Archiving from £2.00</li><li>Email Protection from £1.50</li><li>Office Suite from £5.99</li></ul>
    <span class="btn-outline">READ MORE</span>
  </div>
  <div class="price-card">
    <h3>CLOUD</h3>
    <h4>Reduce Costs &amp; Increase Performance</h4>
    <ul><li>Online Backup</li><li>Private Cloud Servers</li><li>Virtual Desktop</li></ul>
    <span class="btn-outline">READ MORE</span>
  </div>
</div>

<section class="tech">
  <div class="tech-photo" role="img" aria-label="Photo of a smiling support engineer wearing a headset"></div>
  <h2>Technical Support</h2>
  <p>Our highly skilled and certified engineers are on hand to support your business and utilise advanced technologies to proactively monitor and maintain your systems 24/7 and prevent errors before they occur.</p>
  <span class="btn-light">READ MORE</span>
</section>

<footer class="site-footer">
  <div class="footer-col" style="left:40px">
    <h5>SEND MESSAGE</h5>
    <div class="form-field">Name</div>
    <div class="form-field">E-mail</div>
    <div class="form-field tall">Message</div>
    <div class="btn-submit"><svg width="18" height="14" viewBox="0 0 18 14"><rect x="1" y="1" width="16" height="12" fill="none" stroke="#fff" stroke-width="2"/><path d="M1 1l8 6 8-6" fill="none" stroke="#fff" stroke-width="2"/></svg>SUBMIT</div>
  </div>
  <div class="footer-col" style="left:456px">
    <h5>CONTACT US</h5>
    <div class="contact-item"><span class="bullet"></span><div>Harbourside Quay<br>e: sales@brightmend.co.uk</div></div>
    <div class="contact-item"><span class="bullet"></span><div>Support<br>support@brightmend.co.uk</div></div>
    <div class="contact-item"><span class="bullet"></span><div>Sales<br>sales@brightmend.co.uk</div></div>
  </div>
  <div class="footer-col" style="left:756px">
    <h5>MENU</h5>
    <ul class="footer-menu"><li>Home</li><li>Support</li><li>Services</li><li>About</li><li>Contact</li></ul>
  </div>
  <div class="footer-col" style="left:940px">
    <h5>FOLLOW US ON</h5>
    <div class="social"><span></span><span></span><span></span><span></span></div>
  </div>
  <div class="copyright">Copyright © 2015 All Rights Reserved</div>
</footer>

</body>
</html>
```